Small legal and financial translation company needs Squarespace website, brochure and logo

Hello,
We are Lumarin Services (www.lumarinservices-example.com), a boutique legal and financial translation company. We offer our services mainly to Spanish customers. Our primary line of business is the translation of financial statements, but we translate a wide variety legal and financial texts.
The project we are offering comprises three parts: a redo of the current website, an informational brochure for potential customer and a logo design. These three parts should provide a consistent image. We would develop content soon.
We are looking for a website that would look like a typical law firm website, nothing too fancy. Right now, it is in English, Spanish and French, although the new site need only be in English and Spanish. There must be good toggling between the English and Spanish versions. There would be no need for tie-ins to social media and it would not contain a blog. Basically, a static site. We aren't interesting in driving traffic to the site or SEO, as we will contact nearly all potential customers beforehand. The website must be built in Squarespace to enable a smooth transition. The content would be similar to the current page, we'll be working on the exact content, but a rough draft is attached.
The brochure will be some three pages and would introduce the company to potential customers, using similar images as the website and the logo to be designed.
The only specifications for the logo is, as the website and brochure, it convey a sense of security and trust.
Feel free to ask with any questions as this is the first time we have used this platform.
Thank you!
Updates

I've added a more or less final version for the text in the brochure and updated the brief. Added Wednesday, June 10, 2015

Target Market(s)

Spanish law firms, auditors, accountants, banks, investment firms

Industry/Entity Type

Finance

Logo Text

Lumarin Services

Number of Pages Required

5+ page

Font styles to use
Serif

Requirements
Must have
• The website must be built in Squarespace and have a good option to toggle between English and Spanish versions.
• Brochure must be in both English and Spanish, I'm attaching a rough draft of the information that it will probably have. This should give an idea about what to include and the spacing. I will update it to include the final information.
Nice to have
• Would be nice to have some quality finance- and legal-related images
Should not have
• Vibrant colours

```html
<!DOCTYPE html>
<html lang="en">
<head>
<meta charset="utf-8">
<title>Why Choose Lumarin? – Brochure Page</title>
<link rel="stylesheet" href="https://fonts.googleapis.com/css2?family=Cormorant+Garamond:wght@500;600&family=Crimson+Text:wght@400;700&display=swap">
<style>
  :root {
    --navy: #2a3f7e;
    --ink: #1a1a1a;
    --black: #000000;
    --paper: #ffffff;
    --backdrop: #cfcfcf;
  }
  * { box-sizing: border-box; margin: 0; padding: 0; }
  html, body {
    width: 1200px; height: 1200px; overflow: hidden;
    background: var(--backdrop);
  }
  .page {
    position: absolute; left: 268px; top: 110px;
    width: 699px; height: 991px;
    background: var(--paper);
    overflow: hidden;
  }
  .page-title {
    position: absolute; left: 47px; top: 34px;
    font-family: "Cormorant Garamond", serif;
    font-weight: 500;
    font-variant: small-caps;
    font-size: 38px; letter-spacing: 1.5px;
    color: var(--navy);
  }
  .benefit {
    position: absolute; left: 43px; width: 620px; height: 106px;
  }
  .benefit-icon {
    position: absolute; left: 0; top: 0; width: 106px; height: 106px;
  }
  .benefit-title {
    position: absolute; left: 130px; top: 22px;
    font-family: "Crimson Text", serif;
    font-size: 18px; color: var(--ink); letter-spacing: -0.3px;
  }
  .benefit-text {
    position: absolute; left: 132px; top: 52px; width: 460px;
    font-family: "Crimson Text", serif;
    font-size: 13px; line-height: 20px; color: var(--ink); letter-spacing: -0.3px;
  }
  .benefit-text strong { font-weight: 700; color: var(--black); }
  .footer-shape { position: absolute; left: 0; top: 0; width: 699px; height: 991px; }
  .footer-url {
    position: absolute; left: 24px; top: 951px;
    font-family: "Crimson Text", serif;
    font-size: 18px; color: var(--paper);
  }
</style>
</head>
<body>
<main class="page">
  <h1 class="page-title">Why Choose Lumarin?</h1>

  <section class="benefit" style="top:111px">
    <svg class="benefit-icon" viewBox="0 0 106 106" aria-hidden="true">
      <circle cx="53" cy="53" r="50" fill="none" stroke="var(--navy)" stroke-width="3.5"/>
      <circle cx="58" cy="30" r="6" fill="var(--navy)"/>
      <ellipse cx="55" cy="55" rx="22" ry="17" fill="var(--navy)"/>
      <path d="M33 46 l-6 -4 l1 9 z M30 52 h-4 v7 h5 z" fill="var(--navy)"/>
      <rect x="38" y="64" width="7" height="12" rx="2" fill="var(--navy)"/>
      <rect x="62" y="64" width="7" height="12" rx="2" fill="var(--navy)"/>
      <circle cx="38" cy="50" r="1.6" fill="var(--paper)"/>
    </svg>
    <h2 class="benefit-title">Save Money</h2>
    <p class="benefit-text">Translations entrusted to a specialist company <strong>save both time and money</strong></p>
  </section>

  <section class="benefit" style="top:275px">
    <svg class="benefit-icon" viewBox="0 0 106 106" aria-hidden="true">
      <circle cx="53" cy="53" r="50" fill="none" stroke="var(--navy)" stroke-width="3.5"/>
      <polygon points="53,26 60.5,45 81,46 65,59 71,79 53,67.5 35,79 41,59 25,46 45.5,45" fill="var(--navy)"/>
    </svg>
    <h2 class="benefit-title">Quality Guaranteed</h2>
    <p class="benefit-text"><strong>Guaranteed quality time</strong> and time again</p>
  </section>

  <section class="benefit" style="top:439px">
    <svg class="benefit-icon" viewBox="0 0 106 106" aria-hidden="true">
      <circle cx="53" cy="53" r="50" fill="none" stroke="var(--navy)" stroke-width="3.5"/>
      <circle cx="47" cy="44" r="9" fill="var(--navy)"/>
      <path d="M29 75 q0 -17 18 -17 q18 0 18 17 z" fill="var(--navy)"/>
      <path d="M47 60 l-2 4 l2 10 l2 -10 z" fill="var(--paper)"/>
      <path d="M60 30 a9 7 0 1 1 6 7 l-5 3 l1 -4 a9 7 0 0 1 -2 -6 z" fill="none" stroke="var(--navy)" stroke-width="2.5"/>
    </svg>
    <h2 class="benefit-title">Native Translators Only</h2>
    <p class="benefit-text">Promise that expert translators work only in their mother tongue</p>
  </section>

  <section class="benefit" style="top:603px">
    <svg class="benefit-icon" viewBox="0 0 106 106" aria-hidden="true">
      <circle cx="53" cy="53" r="50" fill="none" stroke="var(--navy)" stroke-width="3.5"/>
      <path d="M70 44 A20 20 0 1 0 70 62" fill="none" stroke="var(--navy)" stroke-width="4.5"/>
      <polygon points="64,50 78,50 71,59" fill="var(--navy)"/>
      <path d="M52 40 V54 L60 60" fill="none" stroke="var(--navy)" stroke-width="4" stroke-linecap="round"/>
    </svg>
    <h2 class="benefit-title">Consistency Over Time</h2>
    <p class="benefit-text">A <strong>consistent voice</strong> cultivated over time and across channels ensures that your <strong>firm speaks with one voice</strong></p>
  </section>

  <section class="benefit" style="top:767px">
    <svg class="benefit-icon" viewBox="0 0 106 106" aria-hidden="true">
      <circle cx="53" cy="53" r="50" fill="none" stroke="var(--navy)" stroke-width="3.5"/>
      <rect x="32" y="33" width="42" height="28" rx="2" fill="var(--navy)"/>
      <rect x="36" y="37" width="34" height="20" fill="var(--paper)"/>
      <path d="M26 64 h54 l-4 9 h-46 z" fill="var(--navy)"/>
      <polygon points="49,41 49,50 51.5,48 53.5,52 55,51 53,47 56,47" fill="var(--navy)"/>
    </svg>
    <h2 class="benefit-title">Use of Technology Helps Cut Costs</h2>
    <p class="benefit-text" style="line-height:18px">Use of cutting-edge technology helps cut costs by ensuring competitive budgets based on past work</p>
  </section>

  <svg class="footer-shape" viewBox="0 0 699 991" aria-hidden="true">
    <polygon points="532,937 659,880 673,922" fill="var(--navy)"/>
    <polygon points="362,956 699,923 699,984" fill="var(--black)"/>
    <polygon points="0,923 360,958 699,989 699,991 0,991" fill="var(--navy)"/>
  </svg>
  <p class="footer-url">www.lumarinservices-example.com</p>
</main>
</body>
</html>
```